Smile club flyer design

I am launching an office smile club and would like a design that sits my branding and that is appealing to customers. I have a design (I need a new one) that has all the information.
My website is maplehavendentalcarekx.com
Brand color is green. The design can be any color

Target Market(s)

Ages 30+

Industry/Entity Type

Dental

Font styles to use
Serif

Requirements
Must have
• Appealing to patients

```html
<!DOCTYPE html>
<html lang="en">
<head>
<meta charset="utf-8">
<title>Smile Club Membership Flyer</title>
<link rel="stylesheet" href="https://fonts.googleapis.com/css2?family=Poppins:wght@500;600;700;800&family=Roboto+Condensed:wght@500;600&family=Kaushan+Script&family=Libre+Baskerville&display=swap">
<style>
:root{
  --backdrop:#3a3a3a;
  --brand-green:#087a33;
  --deep-green:#1f5a33;
  --orange:#e8820c;
  --teal-dark:#005c50;
  --teal:#16b8a8;
  --amber-dark:#cf7504;
  --amber:#f6a02e;
  --blue-dark:#0448a0;
  --blue:#1a7ef2;
  --lime:#7cb531;
  --night:#06302f;
  --ink:#2e2e2e;
  --white:#ffffff;
}
*{margin:0;padding:0;box-sizing:border-box}
html,body{width:1011px;height:1200px;overflow:hidden;background:var(--backdrop)}
.flyer{position:absolute;left:105px;top:0;width:800px;height:1200px;overflow:hidden;
  background:linear-gradient(180deg,#fff 0,#fff 520px,#eef3ef 560px,#7ea78a 700px,var(--deep-green) 860px,#2d6a40 940px,#cfe0d4 1040px,#fff 1110px);
  font-family:'Poppins',sans-serif}
.abs{position:absolute}
.brand-name{left:57px;top:44px;width:300px;font-family:'Poppins',sans-serif;font-weight:700;color:var(--brand-green);font-size:30px;line-height:1.05}
.intro{left:66px;top:120px;font-family:'Kaushan Script',cursive;font-size:60px;color:#0b3d1c}
.hero-photo{left:371px;top:0;width:429px;height:228px;background:radial-gradient(ellipse at 60% 100%,#1fa25a 0,#2bb06a 35%,rgba(255,255,255,0) 72%),linear-gradient(180deg,#fff,#f3f6f3)}
.headline{left:60px;top:196px;width:690px;text-align:center;font-weight:800;font-size:124px;color:var(--orange);letter-spacing:-3px;line-height:1.1}
.subhead{left:100px;top:313px;width:600px;text-align:center;font-weight:700;font-size:64px;color:var(--brand-green);letter-spacing:-1px}
.tagline{left:59px;top:391px;width:671px;height:44px;border-radius:22px;background:var(--brand-green);color:#fff;font-weight:600;font-size:17px;display:flex;align-items:center;justify-content:center}
.plan{position:absolute;top:447px;width:220px;height:353px}
.plan-body{position:absolute;left:5px;right:5px;top:150px;bottom:0;border-radius:0 0 14px 14px}
.plan-head{position:absolute;left:0;top:0;width:100%;height:183px;border-radius:10px 10px 0 0;clip-path:polygon(0 0,100% 0,100% 87%,50% 100%,0 87%);text-align:center;color:#fff}
.plan-title{margin-top:20px;font-weight:700;font-size:28px;line-height:1.2}
.plan-sub{font-weight:500;font-size:18px;line-height:1.1}
.plan-rule{margin:10px 22px 0;border-top:1px dotted rgba(255,255,255,.35)}
.plan-price{font-weight:800;font-size:50px;line-height:1;margin-top:10px}
.plan-per{font-size:15px;font-weight:500;margin-top:2px}
.perks{position:absolute;left:14px;right:6px;list-style:none;font-family:'Roboto Condensed',sans-serif;font-weight:600;font-size:12.5px;color:#fff;line-height:1.25}
.perks li{position:relative;padding-left:16px;margin-bottom:11px}
.perks li::before{content:"";position:absolute;left:0;top:2px;width:11px;height:11px;border-radius:50%;background:#fff}
.perks li::after{content:"";position:absolute;left:3px;top:4px;width:5px;height:3px;border-left:2px solid currentColor;border-bottom:2px solid currentColor;transform:rotate(-45deg)}
.core .plan-head{background:var(--teal-dark)}.core .plan-body{background:var(--teal)}.core .perks li::after{color:var(--teal)}
.bright .plan-head{background:var(--amber-dark)}.bright .plan-body{background:var(--amber)}.bright .perks li::after{color:var(--amber)}
.total .plan-head{background:var(--blue-dark)}.total .plan-body{background:var(--blue)}.total .perks li::after{color:var(--blue)}
.join{left:39px;top:836px;font-weight:800;font-size:33px;color:var(--amber);letter-spacing:-.5px}
.phone-icon{left:46px;top:896px;width:51px;height:51px}
.phone-number{left:106px;top:884px;font-weight:700;font-size:60px;color:#fff;letter-spacing:-1px}
.financing{left:39px;top:1021px;font-weight:600;font-size:25px;color:var(--ink)}
.partner{top:1079px;font-weight:600;font-size:24px;color:#333}
.fee{left:25px;top:1135px;width:453px;height:43px;border-radius:22px;background:linear-gradient(90deg,#c9f5d9,#7ee8a4);display:flex;align-items:center;padding-left:20px;font-weight:500;font-size:17px;color:#10321c}
.refresh-dark{left:546px;top:990px;width:208px;height:192px;background:var(--night);border-radius:0 0 14px 14px}
.refresh-head{left:540px;top:829px;width:220px;height:184px;background:var(--lime);clip-path:polygon(0 0,100% 0,100% 87%,50% 100%,0 87%);text-align:center;color:#fff}
.new-tab{left:594px;top:816px;width:112px;height:28px;border-radius:14px;background:var(--amber);color:#fff;font-family:'Libre Baskerville',serif;font-size:20px;text-align:center;line-height:28px}
.refresh-title{margin-top:24px;font-weight:800;font-size:46px;line-height:1}
.refresh-sub{font-size:14px;font-weight:500}
.refresh-rule{margin:10px 20px 0;border-top:1px dotted rgba(255,255,255,.5)}
.refresh-price{font-weight:800;font-size:46px;margin-top:4px}
.refresh-perks{left:565px;top:1027px;list-style:none;font-family:'Roboto Condensed',sans-serif;font-weight:600;font-size:16px;color:#fff}
.refresh-perks li{position:relative;padding-left:17px;margin-bottom:6px}
.refresh-perks li::before{content:"";position:absolute;left:0;top:6px;width:11px;height:11px;border-radius:50%;background:var(--amber)}
.refresh-rule2{left:560px;top:1122px;width:180px;border-top:1px dotted rgba(255,255,255,.35)}
.limited{left:560px;top:1130px;width:190px;text-align:center;font-family:'Kaushan Script',cursive;font-size:22px;color:var(--amber)}
</style>
</head>
<body>
<main class="flyer">
  <div class="abs brand-name">Maplehaven<br>Dental Care</div>
  <div class="abs intro">Introducing</div>
  <div class="abs hero-photo" role="img" aria-label="Smiling woman in a green sweater pointing at her smile"></div>
  <h1 class="abs headline">SMILE CLUB</h1>
  <h2 class="abs subhead">MEMBERSHIP</h2>
  <div class="abs tagline">AFFORDABLE DENTAL CARE &nbsp;- NO INSURANCE REQUIRED</div>

  <section class="plan core" style="left:47px">
    <div class="plan-body"><ul class="perks" style="top:72px">
      <li>Comprehensive Annual Exam</li><li>2 Professional Cleanings per Year</li><li>Routine Bitewing X-rays</li><li>10% Savings on Treatment</li></ul></div>
    <div class="plan-head"><div class="plan-title">CORE CARE</div><div class="plan-sub">PREVENTIVE</div><div class="plan-rule"></div><div class="plan-price">$39</div><div class="plan-per">/MONTH</div></div>
  </section>
  <section class="plan bright" style="left:290px">
    <div class="plan-body"><ul class="perks" style="top:72px">
      <li>Annual In-Office Whitening<br>(Top &amp; Bottom)</li><li>Custom Whitening Trays</li><li>15% Savings on Elective Treatment</li></ul></div>
    <div class="plan-head"><div class="plan-title">BRIGHT</div><div class="plan-sub">COSMETIC</div><div class="plan-rule"></div><div class="plan-price">$59</div><div class="plan-per">/MONTH</div></div>
  </section>
  <section class="plan total" style="left:535px">
    <div class="plan-body"><ul class="perks" style="top:58px">
      <li>3-4 Perio Maintenance<br>Visits per Year</li><li>1 Comprehensive Exam</li><li>Diagnostic X-rays</li><li>15% Savings on Restorative &amp;<br>Elective Care</li></ul></div>
    <div class="plan-head"><div class="plan-title">TOTAL SMILE</div><div class="plan-sub">PERIODONTAL</div><div class="plan-rule"></div><div class="plan-price">$89</div><div class="plan-per">/MONTH</div></div>
  </section>

  <div class="abs join">JOIN SMILE CLUB TODAY!</div>
  <svg class="abs phone-icon" viewBox="0 0 51 51" aria-hidden="true">
    <circle cx="25.5" cy="25.5" r="25.5" fill="#7cb531"/>
    <path d="M19 15c1-1 2-1 3 0l3 4c.6 1 .4 2-.4 2.7l-1.6 1.3c1 2.5 3 4.5 5.5 5.5l1.3-1.6c.7-.8 1.7-1 2.7-.4l4 3c1 1 1 2 0 3l-2 2c-1.5 1.3-4 1.3-7-.5-4-2.4-7-5.4-9.3-9.3-1.8-3-1.8-5.5-.5-7z" fill="#fff"/>
  </svg>
  <div class="abs phone-number">555-318-4620</div>

  <div class="abs financing">FLEXIBLE FINANCING FOR TREATMENT</div>
  <div class="abs partner" style="left:35px">FlexPay</div>
  <div class="abs partner" style="left:237px">Bloomfin</div>
  <div class="abs fee">*$49 Lifetime Activation Fee (Non-Refundable)</div>

  <div class="abs refresh-dark"></div>
  <div class="abs refresh-head"><div class="refresh-title">SMILE</div><div class="refresh-sub">REFRESH PACKAGE</div><div class="refresh-rule"></div><div class="refresh-price">$499</div></div>
  <div class="abs new-tab">New</div>
  <ul class="abs refresh-perks"><li>Cleaning</li><li>Comprehensive Exam</li><li>Whitening</li></ul>
  <div class="abs refresh-rule2"></div>
  <div class="abs limited">Limited Time Offer</div>
</main>
</body>
</html>
```